Brintel Works - Fast, Efficient and Gas Mainteance for Domestic, Commercial and Industrial clients

We are in the process of purchasing a new business and would like to get a new logo and business card.
Business is a gas maintenance business that also does new gas installations.
Has been established since 1988.
Services include:
Install all types of gas appliances & equipment inc. hot water units
Maintain / repair / replace all types of gas appliances & equipment

Target Market(s)

Domestic, Commercial and Industrial clients

Industry/Entity Type

Business

Contact Information for Business Card

admin@brintelworks.com.au
07 3918 4726
Brintel Works PTY LTD

Logo Text

Gas Fitting & Plumbing Maintenance Specialists

Font styles to use
Sans Serif

Requirements
Must have
• Logo
• Business name, contact number, email address, web address
• Domestic | Commercial | Industrial Est Since 1988
Nice to have
• Possibly a black card with a flame logo to one side
Should not have
• Spelling errors

```html
<!DOCTYPE html>
<html lang="en">
<head>
<meta charset="utf-8">
<title>Brintel Works – Business Card</title>
<link href="https://fonts.googleapis.com/css2?family=Source+Sans+3:wght@400;700;900&display=swap" rel="stylesheet">
<style>
  :root {
    --stage: #161616;
    --paper: #ffffff;
    --flame-red: #e8262a;
    --flame-orange: #f07a22;
    --flame-yellow: #fcd116;
    --ink-red: #e3232b;
    --emboss-light: rgba(255, 240, 170, 0.35);
    --emboss-shade: rgba(150, 40, 0, 0.35);
  }
  * { margin: 0; padding: 0; box-sizing: border-box; }
  html, body {
    width: 1200px; height: 900px; overflow: hidden;
    background: var(--stage);
    font-family: "Source Sans 3", sans-serif;
  }
  .stage { position: relative; width: 1200px; height: 900px; }
  .card {
    position: absolute; top: 170px;
    width: 347px; height: 561px;
  }
  .card-front { left: 259px; background: var(--paper); color: var(--ink-red); text-align: center; }
  .card-back {
    left: 631px;
    background: linear-gradient(180deg, var(--flame-yellow) 0%, var(--flame-orange) 50%, var(--flame-red) 100%);
  }
  .accent-band { position: absolute; left: 102px; width: 143px; }
  .accent-band--top {
    top: 0; height: 30px;
    background: linear-gradient(180deg, var(--flame-yellow), var(--flame-orange) 55%, var(--flame-red));
  }
  .accent-band--bottom {
    bottom: 0; height: 28px;
    background: linear-gradient(180deg, var(--flame-red), var(--flame-orange) 45%, var(--flame-yellow));
  }
  .brand-mark {
    position: absolute; top: 84px; left: 124px;
    width: 100px; height: 100px; border-radius: 50%;
    background: linear-gradient(180deg, var(--flame-yellow), var(--flame-orange) 50%, var(--flame-red));
  }
  .brand {
    position: absolute; top: 201px; left: 0; width: 100%;
  }
  .brand-name {
    font-weight: 900; font-size: 39px; line-height: 1; letter-spacing: 0.2px;
    color: var(--ink-red);
  }
  .brand-suffix {
    margin-top: 2px; font-weight: 700; font-size: 12px; letter-spacing: 1.6px;
    color: var(--ink-red);
  }
  .contact-list {
    position: absolute; top: 285px; left: 0; width: 100%;
    list-style: none; font-size: 16.5px; line-height: 20px;
  }
  .contact-list li { display: flex; justify-content: center; align-items: center; gap: 7px; }
  .contact-icon { width: 10px; height: 10px; flex: none; }
  .address {
    position: absolute; top: 371px; left: 0; width: 100%;
    font-size: 16.5px; line-height: 20px; font-style: normal;
  }
  .sectors {
    position: absolute; top: 437px; left: 0; width: 100%;
    font-size: 16.5px; line-height: 20px;
  }
  .back-mark {
    position: absolute; top: 115px; left: 44px;
    width: 260px; height: 260px; border-radius: 50%;
    box-shadow: inset 2px 2px 3px var(--emboss-light), inset -2px -2px 3px var(--emboss-shade),
                1px 1px 2px var(--emboss-shade);
  }
</style>
</head>
<body>
<main class="stage">
  <section class="card card-front" aria-label="Business card front">
    <div class="accent-band accent-band--top"></div>

    <div class="brand-mark" role="img" aria-label="Brand mark"></div>

    <header class="brand">
      <div class="brand-name">Brintel Works</div>
      <div class="brand-suffix">PTY LTD</div>
    </header>

    <ul class="contact-list">
      <li>
        <svg class="contact-icon" viewBox="0 0 10 10" aria-hidden="true">
          <path d="M2 0.5 L3.6 2.6 L2.7 3.6 Q3.8 5.9 6.3 7.3 L7.4 6.4 L9.5 8 L8.3 9.5 Q2.5 8.6 0.5 1.7 Z" fill="var(--flame-orange)"/>
        </svg>
        <span>07 3918 4726</span>
      </li>
      <li>
        <svg class="contact-icon" viewBox="0 0 10 10" aria-hidden="true">
          <rect x="0.5" y="2" width="9" height="6.5" fill="var(--flame-orange)"/>
          <path d="M0.5 2 L5 5.8 L9.5 2" fill="none" stroke="#fff" stroke-width="0.9"/>
        </svg>
        <span>admin@brintelworks.com.au</span>
      </li>
      <li>
        <svg class="contact-icon" viewBox="0 0 10 10" aria-hidden="true">
          <circle cx="5" cy="5" r="4.5" fill="var(--flame-orange)"/>
          <path d="M0.5 5 H9.5 M5 0.5 Q2.5 5 5 9.5 M5 0.5 Q7.5 5 5 9.5" fill="none" stroke="#fff" stroke-width="0.7"/>
        </svg>
        <span>www.brintelworks.com.au</span>
      </li>
    </ul>

    <address class="address">12345, Address Goes Here<br>Country Name, 123456.</address>

    <p class="sectors">Domestic | Commercial<br>Industrial Est Since 1988</p>

    <div class="accent-band accent-band--bottom"></div>
  </section>

  <section class="card card-back" aria-label="Business card back">
    <div class="back-mark" role="img" aria-label="Embossed brand mark"></div>
  </section>
</main>
</body>
</html>
```